Maple Crest Cabins Needs a Flyer

We need a new flyer for our Cove Corner Pub. (Photos attached)

We would like to place the bar close to a nice swimming pool that would be in someone's back yard in Florida.

1. Add solar panels. Solar is installed on rails so they sit 2"-3" off the roof.
3. Add a still frame of the Raleigh Herons football game on the TV.
4. The over all color scheme should be colors that compliment pools and
back patios like blues. Not green or orange. Don't try to match our
logo.

4. Make the bar and pool the central main photo.

Here is some copy for the flyer:

"Your pool is lonely! Introducing our stunning solar powered Cove Corner Pub!"

"Expand the value of your outdoor living with the ultimate Entertianment venue"

Bullets:

- Dimensions: 5' deep x 10' wide x 9-6'. Enough seating for 6-8 people.
- Comes FULLY assembled. You can't reach this level of quality in a kit.
- 1 coat of primer, two coats of Harlow Pemberton Crestline paint for
extreme weather.
- 150 MPH rated Dalby Fenwick shingles
- TV mount included in the base configuration.
- Options include, pendant lights, hard surface floor, flip up shelf on short
side, bar stools, cabinets, portable sinks, keg tap installs. wine shelves ,
copper wine glasses, liquor shelves and more!

"Solar versions have enough solar and batteries to power your TV, lights, mini fridge, cell phones and more. The advanced Lithium Phosphate Batteries are very safe and can power everything for up to 48 hours without sun."

"Visit our website and mention "Porch Breeze" in the comments section and receive a free Kodo cooler when you order your new Cove Corner Pub!"

"Visit www.MapleCrestCabins.com/CoveCornerPub to learn more!"

```html
<!DOCTYPE html>
<html lang="en">
<head>
<meta charset="utf-8">
<title>Maple Crest Cabins – Cove Corner Pub Flyer</title>
<link href="https://fonts.googleapis.com/css2?family=Montserrat:wght@400;500;600;700;800;900&family=Barlow+Semi+Condensed:wght@600;700;800&display=swap" rel="stylesheet">
<style>
  :root{
    --navy:#0b2a5b;
    --green:#3f8a2f;
    --footer-green:#5ca33d;
    --orange:#f0a81c;
    --orange-deep:#e9a016;
    --text:#1d1d1d;
    --page:#ececec;
    --white:#ffffff;
  }
  *{margin:0;padding:0;box-sizing:border-box}
  html,body{width:783px;height:1200px;overflow:hidden;background:var(--page)}
  body{font-family:"Montserrat",Arial,sans-serif;color:var(--text);position:relative}

  .flyer{position:absolute;left:0;top:47px;width:783px;height:1106px;background:var(--white);overflow:hidden}

  .pool-photo{position:absolute;left:0;top:0;width:470px;height:580px;
    background:linear-gradient(180deg,#f4f9fc 0%,#e4f3fa 18%,#9fdcef 38%,#49c0e2 58%,#2fb2da 72%,#c8b89c 84%,#ffffff 100%)}
  .bar-photo{position:absolute;left:402px;top:0;width:381px;height:405px;
    background:linear-gradient(160deg,#8fa87a 0%,#6b6f66 25%,#2f3236 45%,#9b6a3e 62%,#3a3c40 80%,#b0a99a 100%)}
  .detail-photo{position:absolute;border-radius:50%;border:4px solid var(--white);box-shadow:0 2px 6px rgba(0,0,0,.15)}
  .detail-opener{left:363px;top:406px;width:188px;height:188px;background:radial-gradient(circle at 40% 45%,#d9c49a,#7d6a4c 55%,#4b3a2a)}
  .detail-wine{left:539px;top:392px;width:210px;height:210px;background:linear-gradient(180deg,#55493b 0%,#9c8a62 40%,#3a2a22 60%,#a4523a 85%,#6d2c22 100%)}

  .brand{position:absolute;left:45px;top:70px;display:flex;align-items:center;gap:8px;
    font-weight:800;font-size:17px;color:var(--orange-deep);letter-spacing:.3px;text-transform:uppercase}
  .brand-dot{width:14px;height:14px;border-radius:50%;background:var(--green)}

  .headline{position:absolute;left:45px;top:146px;font-weight:900;letter-spacing:-2px;line-height:.98;text-transform:uppercase}
  .headline .line-1{display:block;font-size:51px;color:var(--navy)}
  .headline .line-2{display:block;font-size:57px;color:var(--green)}
  .intro{position:absolute;left:47px;top:264px;font-weight:600;font-size:14.5px;line-height:1.3;color:var(--navy);text-transform:uppercase;letter-spacing:.2px}

  .section-title{position:absolute;left:48px;top:523px;font-family:"Barlow Semi Condensed","Arial Narrow",sans-serif;font-weight:700;font-size:17px;line-height:1.2;text-transform:uppercase;color:var(--text)}
  .section-title em{font-style:normal;color:var(--orange-deep)}
  .section-rule{position:absolute;left:48px;top:593px;width:46px;height:3px;background:var(--green)}

  .features{position:absolute;left:48px;top:617px;width:300px;list-style:none}
  .features li{display:flex;gap:14px;font-weight:700;font-size:12.3px;line-height:1.13;margin-bottom:14px}
  .features svg{flex:0 0 15px}

  .options{position:absolute;left:48px;top:851px;display:flex;gap:0}
  .options ul{list-style:none}
  .options .col-a{width:155px}
  .options .col-b{width:200px;margin-top:2px}
  .options li{display:flex;gap:14px;font-weight:600;font-size:12.3px;line-height:1.05;margin-bottom:9px;white-space:nowrap}
  .options svg{flex:0 0 15px}

  .solar-copy{position:absolute;left:437px;top:622px;width:272px;font-size:12.3px;line-height:1.27;font-weight:500}

  .promo{position:absolute;left:438px;top:733px;width:302px;height:114px;background:var(--orange);border-radius:10px;padding:5px}
  .promo-inner{height:100%;border:1.5px dashed rgba(255,255,255,.85);border-radius:7px;text-align:center;padding-top:16px;color:var(--white)}
  .promo-lead{font-family:"Barlow Semi Condensed","Arial Narrow",sans-serif;font-weight:700;font-size:14px;text-transform:uppercase}
  .promo-code{font-weight:900;font-size:34px;line-height:1.05;color:var(--green);text-transform:uppercase;letter-spacing:-1px}
  .promo-tail{font-family:"Barlow Semi Condensed","Arial Narrow",sans-serif;font-weight:700;font-size:14px;text-transform:uppercase}

  .cooler-photo{position:absolute;left:436px;top:862px;width:104px;height:100px;border-radius:10px;background:linear-gradient(180deg,#e84a6f,#c71f4d 60%,#8d1738)}
  .gift{position:absolute;left:553px;top:861px;text-transform:uppercase;font-weight:800;font-size:17px;line-height:1.34}
  .gift .accent{color:var(--green)}
  .gift-product{position:absolute;left:438px;top:975px;width:310px;white-space:nowrap;font-weight:900;font-size:28px;color:var(--orange-deep);letter-spacing:-.8px;text-transform:uppercase}

  .footer{position:absolute;left:0;top:1021px;width:783px;height:85px;background:var(--footer-green);color:var(--white)}
  .footer-photo{position:absolute;left:-22px;top:-4px;width:108px;height:93px;border-radius:0 50% 50% 0;background:linear-gradient(180deg,#7cc3a8,#2fa8d6 55%,#1b7fb4);border-right:5px solid var(--orange)}
  .footer-contact{position:absolute;left:128px;top:26px;font-size:12px;font-weight:600}
  .footer-contact .row{display:flex;align-items:center;gap:8px}
  .footer-contact .phone{font-size:12.5px;text-transform:uppercase;letter-spacing:.3px}
  .footer-contact .phone strong{font-size:19px;font-weight:700;letter-spacing:.5px}
  .footer-contact .address{font-size:11px;margin-top:3px}
  .footer-divider{position:absolute;left:459px;top:20px;height:44px;border-left:1px dashed rgba(255,255,255,.7)}
  .footer-web{position:absolute;left:475px;top:30px;display:flex;gap:10px;font-size:11.5px;font-weight:700;line-height:1.3}
  .footer-web .lead{color:var(--orange)}
</style>
</head>
<body>
<main class="flyer">
  <div class="pool-photo" role="img" aria-label="Backyard swimming pool with steel ladder and wooden deck"></div>
  <div class="bar-photo" role="img" aria-label="Cove Corner Pub backyard bar with guests seated at the counter"></div>
  <div class="detail-photo detail-opener" role="img" aria-label="Bottle opener mounted on the bar post"></div>
  <div class="detail-photo detail-wine" role="img" aria-label="Wine shelf with hanging copper wine glasses"></div>

  <div class="brand"><span class="brand-dot"></span>Maple Crest Cabins</div>

  <h1 class="headline"><span class="line-1">Your Pool</span><span class="line-2">Is Lonely!</span></h1>
  <p class="intro">Introducing our stunning solar<br>powered Cove Corner Pub!</p>

  <h2 class="section-title">Expand the value of your<br>outdoor living with the ultimate<br><em>Entertainment venue</em></h2>
  <div class="section-rule"></div>

  <ul class="features">
    <li><svg width="15" height="15" viewBox="0 0 16 16"><circle cx="8" cy="8" r="8" fill="#3f8a2f"/><path d="M4.5 8.2l2.3 2.3 4.7-4.7" fill="none" stroke="#fff" stroke-width="1.8"/></svg><span>Dimensions: 5′ deep x 10′ wide x 9-6′.<br>Enough seating for 6-8 people.</span></li>
    <li><svg width="15" height="15" viewBox="0 0 16 16"><circle cx="8" cy="8" r="8" fill="#3f8a2f"/><path d="M4.5 8.2l2.3 2.3 4.7-4.7" fill="none" stroke="#fff" stroke-width="1.8"/></svg><span>Comes FULLY assembled. You can't<br>reach this level of quality in a kit.</span></li>
    <li><svg width="15" height="15" viewBox="0 0 16 16"><circle cx="8" cy="8" r="8" fill="#3f8a2f"/><path d="M4.5 8.2l2.3 2.3 4.7-4.7" fill="none" stroke="#fff" stroke-width="1.8"/></svg><span>1 coat of primer, two coats of<br>Harlow Pemberton Crestline paint for<br>extreme weather.</span></li>
    <li><svg width="15" height="15" viewBox="0 0 16 16"><circle cx="8" cy="8" r="8" fill="#3f8a2f"/><path d="M4.5 8.2l2.3 2.3 4.7-4.7" fill="none" stroke="#fff" stroke-width="1.8"/></svg><span>150 MPH rated Dalby Fenwick<br>shingles</span></li>
    <li><svg width="15" height="15" viewBox="0 0 16 16"><circle cx="8" cy="8" r="8" fill="#3f8a2f"/><path d="M4.5 8.2l2.3 2.3 4.7-4.7" fill="none" stroke="#fff" stroke-width="1.8"/></svg><span>TV mount included in the base<br>configuration.</span></li>
  </ul>

  <div class="options">
    <ul class="col-a">
      <li><svg width="15" height="15" viewBox="0 0 16 16"><circle cx="8" cy="8" r="8" fill="#3f8a2f"/><path d="M4.5 8.2l2.3 2.3 4.7-4.7" fill="none" stroke="#fff" stroke-width="1.8"/></svg><span>Pendant lights</span></li>
      <li><svg width="15" height="15" viewBox="0 0 16 16"><path d="M3 8.5l3 3 7-7" fill="none" stroke="#f0a81c" stroke-width="2"/></svg><span>Hard surface floor</span></li>
      <li><svg width="15" height="15" viewBox="0 0 16 16"><path d="M3 8.5l3 3 7-7" fill="none" stroke="#f0a81c" stroke-width="2"/></svg><span>Flip up shelf<br>on short side,</span></li>
      <li><svg width="15" height="15" viewBox="0 0 16 16"><path d="M3 8.5l3 3 7-7" fill="none" stroke="#f0a81c" stroke-width="2"/></svg><span>Bar stools</span></li>
      <li><svg width="15" height="15" viewBox="0 0 16 16"><path d="M3 8.5l3 3 7-7" fill="none" stroke="#f0a81c" stroke-width="2"/></svg><span>Cabinets</span></li>
    </ul>
    <ul class="col-b">
      <li><svg width="15" height="15" viewBox="0 0 16 16"><path d="M3 8.5l3 3 7-7" fill="none" stroke="#f0a81c" stroke-width="2"/></svg><span>Portable sinks,</span></li>
      <li><svg width="15" height="15" viewBox="0 0 16 16"><path d="M3 8.5l3 3 7-7" fill="none" stroke="#f0a81c" stroke-width="2"/></svg><span>Keg tap installs.</span></li>
      <li><svg width="15" height="15" viewBox="0 0 16 16"><path d="M3 8.5l3 3 7-7" fill="none" stroke="#f0a81c" stroke-width="2"/></svg><span>Wine shelves ,</span></li>
      <li><svg width="15" height="15" viewBox="0 0 16 16"><path d="M3 8.5l3 3 7-7" fill="none" stroke="#f0a81c" stroke-width="2"/></svg><span>Copper wine glasses,</span></li>
      <li><svg width="15" height="15" viewBox="0 0 16 16"><path d="M3 8.5l3 3 7-7" fill="none" stroke="#f0a81c" stroke-width="2"/></svg><span>Liquor shelves and more!</span></li>
    </ul>
  </div>

  <p class="solar-copy">Solar versions have enough solar and batteries to power your TV, lights, mini fridge, cell phones and more. The advanced Lithium Phosphate Batteries are very safe and can power everything for up to 48 hours without sun.</p>

  <div class="promo">
    <div class="promo-inner">
      <div class="promo-lead">Visit our website and mention</div>
      <div class="promo-code">Porch Breeze</div>
      <div class="promo-tail">We would love to talk to you!</div>
    </div>
  </div>

  <div class="cooler-photo" role="img" aria-label="Pink hard-sided cooler"></div>
  <p class="gift">Receive a free<br>Kodo cooler<br><span class="accent">When you order<br>your new</span></p>
  <p class="gift-product">Cove Corner Pub!</p>

  <footer class="footer">
    <div class="footer-photo" role="img" aria-label="Backyard pool"></div>
    <div class="footer-contact">
      <div class="row phone">
        <svg width="11" height="11" viewBox="0 0 24 24"><path d="M6.6 10.8a15.5 15.5 0 006.6 6.6l2.2-2.2a1 1 0 011-.25 11.4 11.4 0 003.6.57 1 1 0 011 1V20a1 1 0 01-1 1A17 17 0 013 4a1 1 0 011-1h3.5a1 1 0 011 1 11.4 11.4 0 00.57 3.6 1 1 0 01-.25 1z" fill="#fff"/></svg>
        <span>Call us now: <strong>803-555-0142</strong></span>
      </div>
      <div class="row address">
        <svg width="10" height="12" viewBox="0 0 20 24"><path d="M10 0a8 8 0 00-8 8c0 6 8 16 8 16s8-10 8-16a8 8 0 00-8-8zm0 11a3 3 0 110-6 3 3 0 010 6z" fill="#fff"/></svg>
        <span>2190 Willow Bend Rd, Fort Mill, SC 29715</span>
      </div>
    </div>
    <div class="footer-divider"></div>
    <div class="footer-web">
      <svg width="12" height="12" viewBox="0 0 24 24" style="margin-top:1px"><circle cx="12" cy="12" r="10" fill="none" stroke="#fff" stroke-width="2"/><path d="M2 12h20M12 2c3 3 3 17 0 20M12 2c-3 3-3 17 0 20" fill="none" stroke="#fff" stroke-width="1.6"/></svg>
      <span><span class="lead">VISIT</span> www.MapleCrestCabins.com/<br>CoveCornerPub to learn more!</span>
    </div>
  </footer>
</main>
</body>
</html>
```